Business Card for Vorla Parts Wholesale supplier

Hi There! I need a new business card for our company. We are specialized in selling Vorla parts, mostly we sell new LCD screens for Zelnar and Drelks. I would like to see that back in the design.

You can find the colors and logo's on our website: www.hartuvo.nl

Industry/Entity Type

Business

Contact Information for Business Card

My Details:
Tobias Lindqvist

Phone: 0031687203316
E-mail: Tobias@hartuvo.nl

Slogan: "Because Quality Matters"

Font styles to use
Sans Serif

Colors

Designer to choose colors to be used in the design.

Requirements
Must have
• A Black backside with the Hartuvo logo on it. The front side should be clean with only my contact details.
• But I'm also open for something really different or awesome!
Nice to have
• Remember that we are in the parts & repairing industry, So i'll be handing those business cards mainly to repair companies. Maybe you can do something with that thought :)

```html
<!DOCTYPE html>
<html lang="en">
<head>
<meta charset="utf-8">
<title>Hartuvo Business Card</title>
<link href="https://fonts.googleapis.com/css2?family=Roboto:wght@400;500;700&family=Ubuntu:wght@400&display=swap" rel="stylesheet">
<style>
  :root {
    --backdrop: #e4e4e4;
    --card-black: #1c1c1c;
    --card-black-light: #2e2e2e;
    --card-white: #f7f7f7;
    --ink: #1a1a1a;
    --ink-soft: #333333;
    --orange: #e8671c;
    --divider: #cfcfcf;
    --white: #ffffff;
  }
  * { margin: 0; padding: 0; box-sizing: border-box; }
  html, body {
    width: 1200px;
    height: 576px;
    overflow: hidden;
    background: var(--backdrop);
    font-family: "Roboto", sans-serif;
  }
  .canvas { position: relative; width: 1200px; height: 576px; }

  .card {
    position: absolute;
    top: 138px;
    width: 484px;
    height: 294px;
    border-radius: 13px;
    overflow: hidden;
  }

  /* Back side */
  .card--back { left: 82px; background: var(--card-black); }
  .card-back__photo {
    position: absolute;
    inset: 0;
    background:
      radial-gradient(ellipse 70% 45% at 60% 30%, var(--card-black-light), transparent 70%),
      linear-gradient(160deg, #262626 0%, #1d1d1d 55%, #151515 100%);
  }
  .brand {
    position: absolute;
    display: flex;
    align-items: center;
  }
  .brand--back { left: 104px; top: 114px; gap: 20px; }
  .brand__mark {
    width: 48px;
    height: 48px;
    background: var(--orange);
    border-radius: 10px;
  }
  .brand__name {
    font-family: "Roboto", sans-serif;
    font-weight: 700;
    line-height: 1;
  }
  .brand--back .brand__name { color: var(--white); font-size: 52px; }

  /* Front side */
  .card--front { left: 602px; width: 481px; height: 292px; background: var(--card-white); }
  .brand--front {
    left: 40px;
    top: 80px;
    width: 170px;
    flex-direction: column;
    gap: 12px;
  }
  .brand--front .brand__mark { width: 56px; height: 56px; border-radius: 12px; }
  .brand--front .brand__name { color: var(--ink); font-size: 42px; }

  .divider {
    position: absolute;
    left: 241px;
    top: 72px;
    width: 1px;
    height: 136px;
    background: var(--divider);
  }

  .contact { position: absolute; left: 280px; top: 84px; }
  .contact__name { font-size: 18px; font-weight: 700; color: var(--ink); line-height: 1.1; }
  .contact__role { font-size: 11px; color: var(--ink-soft); margin-top: 4px; }
  .contact__list { list-style: none; margin-top: 22px; }
  .contact__item {
    display: flex;
    align-items: center;
    gap: 9px;
    font-size: 12px;
    color: var(--ink);
    height: 17px;
  }
  .contact__icon { width: 10px; height: 10px; fill: var(--orange); flex: none; }

  .card-front__band { position: absolute; left: 0; bottom: 0; width: 481px; height: 38px; }
  .slogan {
    position: absolute;
    left: 250px;
    bottom: 10px;
    width: 200px;
    text-align: center;
    font-family: "Ubuntu", sans-serif;
    font-size: 12.5px;
    color: var(--white);
  }
</style>
</head>
<body>
<main class="canvas">

  <section class="card card--back" aria-label="Card back">
    <div class="card-back__photo" role="img" aria-label="Dark close-up photo of a smartphone with a cracked screen"></div>
    <div class="brand brand--back">
      <span class="brand__mark"></span>
      <span class="brand__name">hartuvo</span>
    </div>
  </section>

  <section class="card card--front" aria-label="Card front">
    <div class="brand brand--front">
      <span class="brand__mark"></span>
      <span class="brand__name">hartuvo</span>
    </div>

    <div class="divider"></div>

    <div class="contact">
      <p class="contact__name">Tobias Lindqvist</p>
      <p class="contact__role">Managing Director</p>
      <ul class="contact__list">
        <li class="contact__item">
          <svg class="contact__icon" viewBox="0 0 10 10" aria-hidden="true"><path d="M1 3.2C1 2 2.5 1.3 5 1.3S9 2 9 3.2V4H7V3.1H3V4H1z M2 5h6l1 3.7H1z"/></svg>
          0031687203316
        </li>
        <li class="contact__item">
          <svg class="contact__icon" viewBox="0 0 10 10" aria-hidden="true"><path d="M5 .5a4.5 4.5 0 1 0 0 9 4.5 4.5 0 0 0 0-9zm0 1c.5.6.9 1.6 1 2.8H4c.1-1.2.5-2.2 1-2.8zM1.6 4.3A3.5 3.5 0 0 1 3.5 1.8 6 6 0 0 0 3 4.3zm0 1.4H3c.1.9.3 1.8.5 2.5a3.5 3.5 0 0 1-1.9-2.5zM5 8.5c-.5-.6-.9-1.6-1-2.8h2c-.1 1.2-.5 2.2-1 2.8zm1.5-.3c.2-.7.4-1.6.5-2.5h1.4a3.5 3.5 0 0 1-1.9 2.5zM7 4.3a6 6 0 0 0-.5-2.5 3.5 3.5 0 0 1 1.9 2.5z"/></svg>
          Tobias@hartuvo.nl
        </li>
        <li class="contact__item">
          <svg class="contact__icon" viewBox="0 0 10 10" aria-hidden="true"><path d="M.5 2h9v6h-9z M1 2.3 5 5.6 9 2.3" stroke="#f7f7f7" stroke-width=".8"/></svg>
          www.hartuvo.nl
        </li>
      </ul>
    </div>

    <svg class="card-front__band" viewBox="0 0 481 38" aria-hidden="true">
      <polygon points="0,18 215,18 205,38 0,38" fill="var(--card-black)"/>
      <polygon points="232,0 481,0 481,38 205,38" fill="var(--orange)"/>
    </svg>
    <p class="slogan">Because Quality Matters</p>
  </section>

</main>
</body>
</html>
```